Dew and Willow med spa needs an awesome eye catching billboard ad

We need a billboard ad design for a Med Spa with location sin Davenport and Windermere FL A medical spa where the beauty of nature meets the power of science to treat the whole person, mind, body and soul.

Marigold Radiance Med Spa is a medical spa where the beauty of nature meets the power of science to create gorgeous, youthful looking skin. Located in Davenport, Florida, but also serving Four Corners, Celebration, and Windermere, Florida, the talented professional team brings decades of experience in world-class skin care to provide holistic, science-backed aesthetic services and health coaching.

Industry/Entity Type

Spa

Colors
fbee3e
fece3e
eea4c8
e667a6
fbee3d

Requirements
Must have
• Locations in Davenport and Dr Phillips
Phone 407-555-0148
website www.dewandwillow-example.com

Boards for each:
Aesthetic Treatments
Cosmetic Injectables
Quoria facial
add color vs too many earthtones, to catch the eye perhaps using yellow, something that catches the eye and stands out from the normal everyday
Thank you!!!!
Nice to have
• Boards for each:
Aesthetic Treatments
Cosmetic Injectables
Quoria facial
add color vs too many earthtones, to catch the eye
photos that match services,
Thank you!!!!

```html
<!DOCTYPE html>
<html lang="en">
<head>
<meta charset="utf-8">
<title>Marigold Radiance Med Spa – Aesthetic Treatments Billboard</title>
<link rel="stylesheet" href="https://fonts.googleapis.com/css2?family=Philosopher:wght@700&family=Cormorant+Garamond:wght@600&family=Open+Sans:wght@700;800&display=swap">
<style>
  :root {
    --peach: #fdf3e0;
    --rust: #9e5330;
    --pink: #e667a6;
    --pink-soft: #eea4c8;
    --yellow: #fbee3e;
    --marigold: #fece3e;
    --white: #ffffff;
    --photo-warm: #f3c9a8;
    --photo-light: #fdf5e6;
    --photo-hair: #7a5446;
    --photo-top: #eea4c8;
  }
  * { margin: 0; padding: 0; box-sizing: border-box; }
  html, body {
    width: 1200px;
    height: 411px;
    overflow: hidden;
    background: var(--peach);
  }
  .billboard {
    position: relative;
    width: 1200px;
    height: 411px;
    background: var(--peach);
    overflow: hidden;
  }
  .headline {
    position: absolute;
    left: 110px;
    top: 18px;
    width: 500px;
    text-align: center;
    font-family: "Philosopher", "Optima", sans-serif;
    font-weight: 700;
    font-size: 98px;
    line-height: 82px;
    color: var(--pink);
    letter-spacing: -0.5px;
  }
  .brand-name {
    position: absolute;
    left: 75px;
    top: 204px;
    width: 530px;
    text-align: center;
    font-family: "Cormorant Garamond", serif;
    font-weight: 600;
    font-size: 31px;
    line-height: 36px;
    letter-spacing: 7px;
    text-transform: uppercase;
    color: var(--rust);
  }
  .locations {
    position: absolute;
    left: 75px;
    top: 292px;
    width: 530px;
    display: flex;
    justify-content: center;
  }
  .locations span {
    background: var(--yellow);
    padding: 4px 18px;
    font-family: "Open Sans", sans-serif;
    font-weight: 700;
    font-size: 20px;
    line-height: 26px;
    letter-spacing: 1px;
    color: var(--rust);
  }
  .hero-photo {
    position: absolute;
    left: 672px;
    top: 0;
    width: 528px;
    height: 353px;
    background:
      radial-gradient(ellipse 30% 40% at 40% 105%, var(--photo-top) 0%, rgba(238,164,200,0) 100%),
      radial-gradient(ellipse 28% 60% at 40% 60%, rgba(122,84,70,0.55) 0%, rgba(122,84,70,0) 100%),
      linear-gradient(90deg, var(--photo-warm) 0%, var(--photo-light) 100%);
  }
  .accent-stripe {
    position: absolute;
    left: 0;
    top: 353px;
    width: 1200px;
    height: 6px;
    background: var(--marigold);
  }
  .contact-bar {
    position: absolute;
    left: 0;
    top: 359px;
    width: 1200px;
    height: 52px;
    background: var(--pink);
    display: flex;
    align-items: center;
    justify-content: center;
    font-family: "Open Sans", sans-serif;
    font-weight: 800;
    font-size: 33px;
    color: var(--white);
    white-space: nowrap;
  }
  .contact-bar .divider { margin: 0 14px; color: var(--yellow); }
</style>
</head>
<body>
  <div class="billboard">
    <h1 class="headline">Aesthetic<br>Treatments</h1>
    <p class="brand-name">Marigold Radiance<br>Med Spa</p>
    <p class="locations"><span>Davenport &amp; Dr Phillips, FL</span></p>
    <div class="hero-photo" role="img" aria-label="Photo of a woman in a straw hat and pink top, eyes closed, in warm sunlight by a waterfront"></div>
    <div class="accent-stripe"></div>
    <div class="contact-bar">
      <span class="phone">407-555-0148</span>
      <span class="divider">|</span>
      <span class="website">www.dewandwillow-example.com</span>
    </div>
  </div>
</body>
</html>
```